Business Card Design

Looking for business card designs for a new business. there will be two cards of the same design (both lots of information below in contact info). We would like the logo diagonally across the card with the information split above and below the logo similar to sketch. happy to look at similar alternatives
Please use same colours as in logo design

Industry/Entity Type

Business

Contact Information for Business Card

Dwight Halloran
mob - 0491 738 204
ph - 02 6148 3920
fax - 02 6148 3975
email - dwight@kestrelbeams.com.au
14 Larkmoor Road, Taminda NSW 2340

Colin Marchetti
mob - 0438 912 557
ph - 02 6148 3920
fax - 02 6148 3975
email - colin@kestrelbeams.com.au

```html
<!DOCTYPE html>
<html lang="en">
<head>
<meta charset="utf-8">
<title>Kestrel Beams – Business Card</title>
<link rel="stylesheet" href="https://fonts.googleapis.com/css2?family=Open+Sans:wght@400;600;700&display=swap">
<style>
  :root {
    --teal: #0b7a78;
    --ink: #111111;
    --text: #222222;
    --paper: #ffffff;
    --backdrop: #ece8e1;
    --edge: #3a3a3a;
  }
  * { box-sizing: border-box; margin: 0; padding: 0; }
  html, body { width: 1200px; height: 1190px; overflow: hidden; }
  body {
    position: relative;
    background: var(--backdrop);
    font-family: "Open Sans", Arial, sans-serif;
    color: var(--text);
  }
  .card {
    position: absolute;
    background: var(--paper);
    border: 2px solid var(--edge);
    border-radius: 28px;
    overflow: hidden;
  }
  .card--front { left: 28px; top: 38px; width: 946px; height: 540px; }
  .card--back  { left: 214px; top: 612px; width: 942px; height: 536px; }

  .brand {
    position: absolute;
    left: 0; right: 0;
    display: flex;
    justify-content: center;
    align-items: center;
    gap: 18px;
  }
  .brand__mark { width: 40px; height: 40px; background: var(--teal); }
  .brand__name {
    font-weight: 700;
    font-size: 78px;
    line-height: 1;
    color: var(--ink);
    letter-spacing: -1px;
  }
  .card--front .brand { top: 82px; }
  .card--back .brand { top: 208px; }

  .holder {
    position: absolute;
    top: 256px; left: 0; right: 0;
    text-align: center;
    font-weight: 700;
    font-size: 29px;
    color: var(--teal);
  }
  .contacts {
    position: absolute;
    top: 334px; left: 0; right: 0;
    display: flex;
    justify-content: center;
    gap: 10px;
    font-size: 23px;
    color: var(--text);
  }
  .contacts__item { display: flex; align-items: center; gap: 4px; }
  .icon { width: 20px; height: 20px; fill: var(--teal); }
  .email {
    position: absolute;
    top: 378px; left: 0; right: 0;
    display: flex;
    justify-content: center;
    align-items: center;
    gap: 6px;
    font-size: 23px;
  }
  .swoosh { position: absolute; left: 0; top: 0; width: 946px; height: 540px; }
  .address {
    position: absolute;
    top: 488px; left: 0; right: 0;
    text-align: center;
    font-size: 23px;
    color: var(--paper);
  }
  .website {
    position: absolute;
    top: 420px; left: 0; right: 0;
    text-align: center;
    font-size: 30px;
    letter-spacing: 3px;
    color: var(--text);
  }
  .website strong { font-weight: 700; }
</style>
</head>
<body>
  <section class="card card--front">
    <svg class="swoosh" viewBox="0 0 946 540" aria-hidden="true">
      <path d="M0 382 C 250 450, 520 495, 946 440 L946 540 L0 540 Z" fill="var(--teal)"/>
      <path d="M0 348 C 230 420, 520 468, 790 462 C 520 470, 230 440, 0 377 Z" fill="var(--ink)"/>
    </svg>
    <div class="brand">
      <span class="brand__mark"></span>
      <span class="brand__name">Kestrel Beams</span>
    </div>
    <h1 class="holder">Colin Marchetti</h1>
    <div class="contacts">
      <span class="contacts__item">
        <svg class="icon" viewBox="0 0 20 20" aria-label="phone"><path d="M5 2 L8 6 L6.5 8 C7.5 10.5 9.5 12.5 12 13.5 L14 12 L18 15 L16 18 C9 18 2 11 2 4 Z"/></svg>
        02 6148 3920
      </span>
      <span class="contacts__item">
        <svg class="icon" viewBox="0 0 20 20" aria-label="mobile"><path d="M6 1 H14 A1 1 0 0 1 15 2 V18 A1 1 0 0 1 14 19 H6 A1 1 0 0 1 5 18 V2 A1 1 0 0 1 6 1 Z M7 4 V12 H13 V4 Z"/></svg>
        0438 912 557
      </span>
      <span class="contacts__item">
        <svg class="icon" viewBox="0 0 20 20" aria-label="fax"><path d="M5 3 H13 V7 H5 Z M2 8 H18 V15 H2 Z M5 13 H15 V17 H5 Z"/></svg>
        02 6148 3975
      </span>
    </div>
    <div class="email">
      <svg class="icon" viewBox="0 0 20 20" aria-label="email"><path d="M2 8 L10 3 L18 8 V17 H2 Z M4 9 L10 13 L16 9 Z" fill-rule="evenodd"/></svg>
      colin@kestrelbeams.com.au
    </div>
    <p class="address">14 Larkmoor Road, Harlow Creek VIC 3921</p>
  </section>

  <section class="card card--back">
    <div class="brand">
      <span class="brand__mark"></span>
      <span class="brand__name">Kestrel Beams</span>
    </div>
    <p class="website">www.<strong>kestrelbeams</strong>.com.au</p>
  </section>
</body>
</html>
```